New Business Card Design

We need a business card design for a new company based in Sydney called "Haven and Hue". This is an online buisness which will have an online store providing imported homewares.
We are looking for something that is different, perhaps even in shape and using the logo that was designed by Pixel Harbor.

Attached document is a basic example I want to see more creative versions.

Target Market(s)

Homewares, Interior Design

Industry/Entity Type

Business

Contact Information for Business Card

Company Logo
Company Name
Industry area
Name
Position
Phone
Email
Website
Motto

Requirements
Must have
• Logo
Nice to have
• Social website logos - Chatterloop, Glimmoraly, Quibbly, Boardlyne, Veltrix+

```html
<!DOCTYPE html>
<html lang="en">
<head>
<meta charset="utf-8">
<title>Haven and Hue – Business Card</title>
<link href="https://fonts.googleapis.com/css2?family=Lato:wght@400;900&display=swap" rel="stylesheet">
<style>
  :root {
    --backdrop: #d9d8d6;
    --paper: #ffffff;
    --ink: #1f1f1f;
    --ink-soft: #2c2c2c;
    --gold: #b8822e;
    --black: #0d0d0d;
    --shadow: rgba(0, 0, 0, 0.18);
  }
  * { margin: 0; padding: 0; box-sizing: border-box; }
  html, body {
    width: 1200px;
    height: 1000px;
    overflow: hidden;
    background: var(--backdrop);
    font-family: "Lato", Arial, sans-serif;
    color: var(--ink);
  }
  .canvas { position: relative; width: 1200px; height: 1000px; }

  .card {
    position: absolute;
    left: 250px;
    width: 700px;
    height: 400px;
    background: var(--paper);
    border-radius: 22px;
    overflow: hidden;
    box-shadow: 0 8px 22px var(--shadow);
  }
  .card--front { top: 55px; }
  .card--back { top: 540px; }

  .wordmark {
    display: flex;
    align-items: center;
    gap: 14px;
    font-weight: 900;
    color: var(--ink);
    white-space: nowrap;
  }
  .wordmark__dot {
    width: 18px;
    height: 18px;
    border-radius: 50%;
    background: var(--gold);
    flex: none;
  }
  .card--front .wordmark {
    position: absolute;
    left: 50%; top: 50%;
    transform: translate(-50%, -50%);
    font-size: 46px;
  }
  .card--back .wordmark {
    position: absolute;
    left: 200px; top: 168px;
    transform: translateX(-50%);
    font-size: 34px;
  }
  .card--back .wordmark__dot { width: 14px; height: 14px; }

  .divider {
    position: absolute;
    left: 400px; top: 88px;
    width: 2px; height: 200px;
    background: var(--gold);
  }

  .details { position: absolute; left: 420px; top: 60px; }
  .details__name { font-weight: 900; font-size: 25px; color: var(--gold); line-height: 1.1; }
  .details__role { font-size: 20px; color: var(--ink-soft); margin-top: 2px; }
  .details__address { font-size: 16px; line-height: 1.3; margin-top: 18px; color: var(--ink-soft); }
  .details__contacts { list-style: none; margin-top: 8px; }
  .details__contacts li {
    display: flex; align-items: center; gap: 8px;
    font-size: 16px; line-height: 1.45; color: var(--ink-soft);
  }
  .details__contacts svg { width: 16px; height: 16px; flex: none; }

  .bands { position: absolute; left: 0; top: 0; width: 700px; height: 400px; }

  .socials {
    position: absolute;
    left: 540px; top: 306px;
    display: grid;
    grid-template-columns: auto auto;
    column-gap: 12px; row-gap: 6px;
    list-style: none;
  }
  .socials li {
    display: flex; align-items: center; gap: 5px;
    font-size: 11px; color: var(--black); white-space: nowrap;
  }
  .socials__dot { width: 9px; height: 9px; border-radius: 50%; background: var(--black); }
</style>
</head>
<body>
<main class="canvas">

  <section class="card card--front" aria-label="Card front">
    <div class="wordmark"><span class="wordmark__dot"></span>Haven and Hue</div>
  </section>

  <section class="card card--back" aria-label="Card back">
    <svg class="bands" viewBox="0 0 700 400" aria-hidden="true">
      <polygon points="0,338 540,338 522,400 0,400" fill="var(--black)"/>
      <polygon points="540,292 700,292 700,400 508,400" fill="var(--gold)"/>
    </svg>

    <div class="wordmark"><span class="wordmark__dot"></span>Haven and Hue</div>

    <div class="divider"></div>

    <div class="details">
      <p class="details__name">Marlo Fenwick</p>
      <p class="details__role">Director</p>
      <p class="details__address">Unit 7, Lantern Lane<br>Harbourview 2000 NSW AU</p>
      <ul class="details__contacts">
        <li>
          <svg viewBox="0 0 16 16"><path d="M3 2h3l1.5 3.5-2 1.2a8 8 0 0 0 3.8 3.8l1.2-2L14 10v3a1 1 0 0 1-1 1A11 11 0 0 1 2 3a1 1 0 0 1 1-1z" fill="var(--gold)"/></svg>
          02 5550 1987
        </li>
        <li>
          <svg viewBox="0 0 16 16"><rect x="1.5" y="3.5" width="13" height="9" fill="var(--gold)"/><path d="M1.5 3.5 8 9l6.5-5.5" fill="none" stroke="var(--paper)" stroke-width="1.2"/></svg>
          mf@havenandhue.com.au
        </li>
        <li>
          <svg viewBox="0 0 16 16" fill="none" stroke="var(--gold)" stroke-width="1.3"><circle cx="8" cy="8" r="6.3"/><ellipse cx="8" cy="8" rx="2.8" ry="6.3"/><path d="M1.7 8h12.6M2.8 4.8h10.4M2.8 11.2h10.4"/></svg>
          www.havenandhue.com.au
        </li>
      </ul>
    </div>

    <ul class="socials" aria-label="Social channels">
      <li><span class="socials__dot"></span>Chatterloop</li>
      <li><span class="socials__dot"></span>Quibbly</li>
      <li><span class="socials__dot"></span>Glimmoraly</li>
      <li><span class="socials__dot"></span>Boardlyne</li>
      <li><span class="socials__dot"></span>Veltrix+</li>
    </ul>
  </section>

</main>
</body>
</html>
```